Institutional website for an IT Consulting company

Web design + HTML + CSS / Bootstrap + JS (interaction) integration in order to extend our existing website brightvale.coop.
Our website is currently aiming only for recruitment and not for customers, we want to provide a fluid transition between customer side website (this project) and recruitment website (existing site).

Ideally we would love the new design to be "inspired" by our actual graphic chart (Colors mainly). It should provide a great user experience and a landing page (or any mean) allowing the visitor to easily switch from the end customer front end (this project), the recruitment front end (existing front end https://www.brightvale.coop/) and the existing member front end (an other existing front end dedicated to members already existing).

In attachment you will find the expected site content mainly a one page with a first level of information and "link" to sub pages (a way to directly access this sub pages should also be provided).

The website should be accessible on mobile device and desktop.

The attachment is in french as it reflect the final site content, but if google translate isn't sufficient to have a general idea of the content, feel free to ask. We would love to have some visual representation for some categories.

Target Market(s)

fortune 500 companies

Industry/Entity Type

It Company

Coding

Coded - Design and coding required

Number of Pages Required

5+ page

Requirements
Must have
• This project must have an easy way to navigate between 3 sub sites, the customer one (the one designed here), the consultant / recruitment one (the existing one at brightvale.coop), the members one.

A one page experience at first leading to detail pages.

Custom made visuals to illustrate each categories.

Inspiration websites : pirog[.]fr ; tasklynn[.]com ; dorvelo[.] com ...

Be inspired by the existing color from our logo and existing website at brightvale[.]coop

```html
<!DOCTYPE html>
<html lang="en">
<head>
<meta charset="utf-8">
<title>Brightvale.coop – Finding the best consultant</title>
<link href="https://fonts.googleapis.com/css2?family=Montserrat:wght@500;600;700&family=Open+Sans:ital,wght@0,400;0,600;0,700;1,400&display=swap" rel="stylesheet">
<style>
:root{
  --teal:#17aeb3;
  --teal-soft:#d6eff0;
  --ink:#1d2222;
  --pine:#0c4d4c;
  --text:#3a3f40;
  --muted:#7b8184;
  --line:#d9dcdd;
  --soft:#f1f1f1;
  --white:#fff;
}
*{box-sizing:border-box;margin:0;padding:0}
html,body{width:1200px;height:5115px;overflow:hidden}
body{font-family:"Open Sans",Arial,sans-serif;color:var(--text);background:var(--white);position:relative}
section,header,footer{position:absolute;left:0;width:1200px}
.abs{position:absolute}
.h2{font-family:Montserrat,Arial,sans-serif;font-weight:700;font-size:42px;color:var(--ink);text-align:center;width:1200px;left:0;letter-spacing:.5px}
.logo{font-family:Montserrat,Arial,sans-serif;font-weight:700;color:var(--pine);font-size:30px;letter-spacing:.3px;display:flex;align-items:center;gap:10px;white-space:nowrap}
.logo .sq{width:18px;height:18px;background:var(--teal)}
/* header */
.site-header{top:0;height:122px}
.util{top:14px;right:110px;font-size:15px;font-weight:600;color:var(--ink);display:flex;gap:16px}
.util span.sep{color:var(--teal)}
.navbtn{top:50px;height:48px;border:2px solid var(--line);font-family:Montserrat,Arial,sans-serif;font-weight:600;font-size:14px;color:var(--ink);display:flex;align-items:center;justify-content:center}
.navbtn.dark{background:var(--ink);color:#fff;border-color:var(--ink)}
/* hero */
.hero{top:122px;height:578px;background:linear-gradient(90deg,#e4e2df,#d8d6d2)}
.hero-photo{left:600px;top:0;width:600px;height:578px;background:linear-gradient(135deg,#cfc9c1,#e9e6e1 55%,#bdb6ac)}
.hero-frame{left:680px;top:58px;width:492px;height:492px;border:22px solid var(--teal)}
.hero h1{left:108px;top:136px;font-family:Montserrat,Arial,sans-serif;color:var(--ink);line-height:1.1}
.hero h1 .a{display:block;font-weight:500;font-size:46px}
.hero h1 .b{display:block;font-weight:700;font-size:60px;margin-top:6px}
.field{top:300px;height:68px;background:#fff;display:flex;align-items:center;padding-left:22px;gap:12px;font-size:13px;color:#9aa0a3}
.search-btn{left:110px;top:406px;width:142px;height:68px;background:var(--teal);color:#fff;font-family:Montserrat,Arial,sans-serif;font-weight:700;font-size:20px;display:flex;align-items:center;justify-content:center}
.dots{left:548px;top:516px;display:flex;gap:10px}
.dots i{width:18px;height:18px;border-radius:50%;border:2px solid #555;display:block}
.dots i.on{background:#555}
/* welcome */
.welcome{top:700px;height:1168px}
.intro-box{top:152px;width:466px;height:210px;border:8px solid var(--pine);padding:28px 26px 0;text-align:center;font-size:17px;line-height:32px;color:var(--text)}
.intro-box::before{content:"";position:absolute;inset:4px;border:1px solid var(--pine)}
.intro-box b{display:block;margin-top:8px;font-family:Montserrat,Arial,sans-serif;color:var(--teal);font-size:20px}
.lead{top:398px;left:150px;width:900px;text-align:center;font-size:17px;line-height:33px;color:var(--ink);font-weight:600}
.feat{display:flex;align-items:center;gap:26px;font-size:19px;line-height:28px;color:var(--ink);font-weight:600}
.ring{width:116px;height:116px;border-radius:50%;border:2px solid #9aa0a3;display:flex;align-items:center;justify-content:center;flex:none}
.subtitle{top:830px;width:1200px;text-align:center;font-size:17px;font-weight:600;color:var(--ink)}
.outline-btn{top:1050px;height:50px;border:2px solid var(--teal);color:var(--teal);font-family:Montserrat,Arial,sans-serif;font-weight:700;font-size:15px;display:flex;align-items:center;justify-content:center}
/* why */
.why{top:1868px;height:522px;background:var(--soft)}
.card{top:142px;width:314px;height:310px;background:#fff;text-align:center;padding:26px 24px 0}
.card h3{font-family:Montserrat,Arial,sans-serif;font-weight:600;font-size:22px;color:var(--ink);margin:10px 0 12px}
.card p{font-size:14px;line-height:25px;color:var(--muted)}
.card a{position:absolute;left:0;right:0;bottom:28px;font-family:Montserrat,Arial,sans-serif;font-weight:700;font-size:15px;color:var(--teal);text-decoration:none}
.card.hl{background:var(--teal)}
.card.hl h3,.card.hl p,.card.hl a{color:#fff}
/* experts */
.experts{top:2390px;height:995px}
.centered{width:1200px;text-align:center;left:0}
.exp-text{font-size:15px;line-height:32px;color:var(--muted)}
.exp-col{top:218px;width:300px;text-align:center;font-size:22px;font-weight:600;color:var(--ink)}
.exp-art{width:156px;height:156px;margin:0 auto 26px;border-radius:50%;background:var(--teal-soft)}
.tile{top:558px;width:232px}
.tile .ph{height:248px}
.tile .badge{position:absolute;left:70px;top:204px;width:90px;height:90px;border-radius:50%;background:#fff;display:flex;align-items:center;justify-content:center;box-shadow:0 2px 6px rgba(0,0,0,.12)}
.tile .cap{margin-top:62px;text-align:center;font-size:22px;line-height:32px;font-weight:600;color:var(--ink)}
/* news */
.news{top:3385px;height:815px;background:var(--soft)}
.news-item{width:476px;height:294px}
.news-item .ph{height:100%}
.news-item .cap{position:absolute;left:0;right:0;bottom:0;height:74px;background:rgba(20,24,25,.62);color:#fff;font-size:19px;line-height:29px;padding:8px 24px}
.ph-star{background:linear-gradient(135deg,#3c3d3e,#6e6f70)}
.ph-hands{background:linear-gradient(135deg,#a9c7d6,#5d7f90 60%,#2e4450)}
.ph-thumbs{background:linear-gradient(135deg,#b9cfb4,#d3a68f 55%,#7c9a86)}
.ph-team{background:linear-gradient(135deg,#e8e6e2,#b8aea4 55%,#6b5e55)}
/* testimonials */
.testimonials{top:4200px;height:515px;background:linear-gradient(90deg,#14b4bd,#11acb6)}
.testimonials .h2{color:#fff;top:60px}
.client{left:110px;top:200px;width:242px;height:112px;border:8px solid #fff;display:flex;align-items:center;justify-content:center;gap:12px;font-family:Montserrat,Arial,sans-serif;font-weight:700;font-size:34px;color:#fff}
.client i{width:22px;height:22px;background:#fff;display:block}
.quote{left:384px;top:186px;width:706px;color:#fff;font-size:15.5px;line-height:29px}
.divider{left:384px;top:318px;width:706px;height:1px;background:rgba(255,255,255,.35)}
.avatar{left:110px;top:328px;width:120px;height:120px;border-radius:50%;background:linear-gradient(160deg,#e7d3c3,#a98a74);border:4px solid #fff}
.who{left:256px;top:358px;color:#fff;font-size:18px;line-height:30px}
.q2{left:384px;top:340px;width:706px;color:#fff;font-style:italic;font-size:15.5px;line-height:28px}
.arrows{left:1030px;top:440px;display:flex;gap:6px}
.arrows i{width:24px;height:24px;border-radius:50%;background:#fff;display:flex;align-items:center;justify-content:center}
/* footer */
.site-footer{top:4715px;height:400px}
.fcol{top:48px}
.fcol h4{font-family:"Open Sans",Arial,sans-serif;font-weight:600;font-size:19px;color:var(--ink);margin-bottom:14px}
.fcol li{list-style:none;font-size:13.5px;line-height:26.5px;color:var(--muted)}
.contact{font-size:14px;color:var(--muted);display:flex;gap:12px;align-items:flex-start;line-height:26px}
.rule{left:110px;top:325px;width:980px;height:1px;background:var(--line)}
.copy{left:110px;top:366px;font-size:14px;color:var(--muted)}
.social{left:946px;top:344px;display:flex;gap:8px}
.social i{width:42px;height:42px;border-radius:50%;border:2px solid var(--line);display:block}
</style>
</head>
<body>

<header class="site-header">
  <div class="abs" style="left:110px;top:38px">
    <div class="logo">BRIGHTVALE.COOP <span class="sq"></span></div>
  </div>
  <nav class="abs util">
    <span>✎ REGISTER</span><span class="sep">|</span><span>LOG IN</span><span class="sep">|</span><span>HELP</span>
  </nav>
  <a class="abs navbtn" style="left:530px;width:150px">I AM BRIGHTVALE</a>
  <a class="abs navbtn" style="left:696px;width:240px">I WISH TO JOIN BRIGHTVALE</a>
  <a class="abs navbtn dark" style="left:954px;width:134px">CONTACT US</a>
</header>

<section class="hero">
  <div class="abs hero-photo" role="img" aria-label="Consultant working at a laptop in a bright office"></div>
  <div class="abs hero-frame"></div>
  <h1 class="abs"><span class="a">FINDING THE BEST</span><span class="b">CONSULTANT</span></h1>
  <div class="abs field" style="left:110px;width:300px">
    <svg width="18" height="18" viewBox="0 0 20 20"><circle cx="8" cy="8" r="6" fill="none" stroke="#555" stroke-width="2.4"/><path d="M12.5 12.5 18 18" stroke="#555" stroke-width="2.6"/></svg>UX Designer...
  </div>
  <div class="abs field" style="left:412px;width:274px">
    <svg width="14" height="18" viewBox="0 0 14 20"><path d="M7 0a7 7 0 0 0-7 7c0 5 7 13 7 13s7-8 7-13a7 7 0 0 0-7-7z" fill="#555"/><circle cx="7" cy="7" r="2.6" fill="#fff"/></svg>Country, Region , City
  </div>
  <a class="abs search-btn">SEARCH</a>
  <div class="abs dots"><i class="on"></i><i></i><i></i><i></i></div>
</section>

<section class="welcome">
  <h2 class="abs h2" style="top:58px">WELCOME TO BRIGHTVALE.COOP</h2>
  <div class="abs intro-box" style="left:110px">Brightvale.coop is a services company with strong values of cooperations,based in particular on an atypical management<b>CAE SCOP</b></div>
  <div class="abs intro-box" style="left:622px">We have independent profiles on subjects such as Stratus BI, infrastructure and security, Data Platform!<b>SEARCH</b></div>
  <p class="abs lead">But why should you chose only one consultant when Brightvale.coop can suggest a whole community to your service! Brightvale is first and foremost a team of experts &nbsp;including also a few MVPs in cooperation with the group of consultants on a daily basis.</p>

  <div class="abs feat" style="left:110px;top:524px"><div class="ring"><svg width="40" height="40" viewBox="0 0 40 40"><rect x="6" y="4" width="28" height="32" rx="2" fill="none" stroke="var(--teal)" stroke-width="3"/><path d="M11 30l7-9 5 6 3-3 4 6z" fill="var(--teal)"/><circle cx="25" cy="13" r="3" fill="var(--teal)"/></svg></div>Hybrid<br>architecture</div>
  <div class="abs feat" style="left:428px;top:524px"><div class="ring"><svg width="36" height="40" viewBox="0 0 36 40"><path d="M18 2 4 8v10c0 10 6 17 14 20 8-3 14-10 14-20V8z" fill="none" stroke="var(--teal)" stroke-width="3.5"/><path d="M18 6v28c-6-3-10-8-10-16V10z" fill="var(--teal)"/></svg></div>Security and<br>infrastructure</div>
  <div class="abs feat" style="left:748px;top:524px"><div class="ring"><svg width="36" height="40" viewBox="0 0 36 40"><ellipse cx="18" cy="7" rx="15" ry="5" fill="var(--teal)"/><path d="M3 12c0 3 7 5 15 5s15-2 15-5v6c0 3-7 5-15 5S3 21 3 18zM3 23c0 3 7 5 15 5s15-2 15-5v6c0 3-7 5-15 5S3 32 3 29z" fill="var(--teal)"/></svg></div>Expertise on Modern<br>Data Warehouse</div>

  <div class="abs feat" style="left:110px;top:670px"><div class="ring"><svg width="46" height="40" viewBox="0 0 46 40"><circle cx="16" cy="22" r="10" fill="none" stroke="var(--teal)" stroke-width="7" stroke-dasharray="4 3.4"/><circle cx="16" cy="22" r="4" fill="var(--teal)"/><circle cx="35" cy="11" r="6" fill="none" stroke="var(--teal)" stroke-width="5" stroke-dasharray="3 2.5"/><circle cx="36" cy="30" r="5" fill="none" stroke="var(--teal)" stroke-width="4" stroke-dasharray="3 2.5"/></svg></div>Training</div>
  <div class="abs feat" style="left:428px;top:670px"><div class="ring"><svg width="46" height="30" viewBox="0 0 46 30"><rect x="2" y="2" width="42" height="26" fill="none" stroke="var(--teal)" stroke-width="4"/><circle cx="23" cy="15" r="7" fill="var(--teal)"/><rect x="7" y="12" width="5" height="6" fill="var(--teal)"/><rect x="34" y="12" width="5" height="6" fill="var(--teal)"/></svg></div>Cost<br>rationalisation<br>on Stratus</div>
  <div class="abs feat" style="left:748px;top:670px"><div class="ring"><svg width="44" height="40" viewBox="0 0 44 40"><rect x="2" y="3" width="40" height="26" rx="2" fill="var(--teal)"/><rect x="6" y="7" width="32" height="18" fill="#fff"/><rect x="18" y="29" width="8" height="6" fill="var(--teal)"/><rect x="12" y="35" width="20" height="3" fill="var(--teal)"/></svg></div>Advanced display,<br>especially via<br>Lumen BI</div>

  <p class="abs subtitle">Our teams are highly oriented on Stratus topics</p>
  <div class="abs feat" style="left:326px;top:888px"><div class="ring"><svg width="56" height="30" viewBox="0 0 56 30"><path d="M12 28a10 10 0 0 1 0-20c2-5 7-8 13-8 7 0 12 4 14 10a9 9 0 0 1 5 18z" fill="var(--teal)" opacity=".85"/></svg></div>Data Platform</div>
  <div class="abs feat" style="left:644px;top:888px"><div class="ring"><svg width="46" height="40" viewBox="0 0 46 40"><path d="M4 4v32h38" fill="none" stroke="var(--teal)" stroke-width="4"/><path d="M10 30l10-11 7 6 13-14" fill="none" stroke="var(--teal)" stroke-width="4"/><path d="M33 9h9v9" fill="none" stroke="var(--teal)" stroke-width="4"/></svg></div>Data &amp; BI</div>

  <a class="abs outline-btn" style="left:236px;width:296px">YOU WISH FOR A QUOTATION</a>
  <a class="abs outline-btn" style="left:554px;width:224px">MORE INFORMATION?</a>
  <a class="abs outline-btn" style="left:802px;width:158px">CONTACT US!</a>
</section>

<section class="why">
  <h2 class="abs h2" style="top:52px">WHY USE A AEC–COPA?</h2>
  <div class="abs card" style="left:110px">
    <svg width="64" height="56" viewBox="0 0 64 56"><rect x="4" y="12" width="40" height="40" rx="5" fill="none" stroke="var(--teal)" stroke-width="4"/><path d="M22 38l4-12 26-24 8 8-26 24z" fill="var(--teal)"/></svg>
    <h3>Custom–made S/E</h3>
    <p>Accordingly to your needs, our consultant will be able to assist you in achieving your projects.</p>
    <a>FIND OUT MORE</a>
  </div>
  <div class="abs card hl" style="left:444px">
    <svg width="70" height="60" viewBox="0 0 70 60"><circle cx="35" cy="14" r="10" fill="#fff"/><circle cx="14" cy="20" r="7" fill="#fff"/><circle cx="56" cy="20" r="7" fill="#fff"/><path d="M18 58c0-18 8-28 17-28s17 10 17 28z" fill="#fff"/><path d="M2 50c0-12 5-20 12-20 4 0 6 2 7 4-3 5-4 10-4 16zM68 50c0-12-5-20-12-20-4 0-6 2-7 4 3 5 4 10 4 16z" fill="#fff"/></svg>
    <h3>A team at your service</h3>
    <p>Brightvale as a AEC–COPA offers you a service, not from an independent to a customer perspective but from a community to a customer</p>
    <a>FIND OUT MORE</a>
  </div>
  <div class="abs card" style="left:776px">
    <svg width="66" height="56" viewBox="0 0 66 56"><path d="M4 4h24l32 32-20 18L4 20z" fill="var(--teal)"/><circle cx="15" cy="15" r="4" fill="#fff"/><path d="M32 4h6l26 28-4 4z" fill="var(--teal)"/></svg>
    <h3>A fair pay</h3>
    <p>At Brightvale, the S/E gain directly what they work for.</p>
    <a>FIND OUT MORE</a>
  </div>
</section>

<section class="experts">
  <h2 class="abs h2" style="top:60px">EXPERTS IN THEIR FIELD</h2>
  <p class="abs centered exp-text" style="top:128px">S/E exports are able to assist you on each standard phase of a data platform project. We also offer formal or<br>custom training but also the capacity of purchasing Stratus credits or Suite 365 licences</p>

  <div class="abs exp-col" style="left:120px">
    <div class="exp-art" role="img" aria-label="Line illustration of a network of connected nodes around a hub"></div>
    Data Platform project
  </div>
  <div class="abs exp-col" style="left:450px">
    <div class="exp-art" role="img" aria-label="Line illustration of a gear framing a trainer"></div>
    Training
  </div>
  <div class="abs exp-col" style="left:780px">
    <div class="exp-art" role="img" aria-label="Line illustration of a cloud linked to circuit lines"></div>
    Cloud Solution Provider
  </div>

  <p class="abs centered exp-text" style="top:458px">In order to find and directly contact the profile(s) that is/are best suited to your needs, please use our research tool.<br>The customer relationship team is also available to answer to all you inquiries:</p>

  <div class="abs tile" style="left:110px"><div class="ph" role="img" aria-label="Hands assembling puzzle pieces on a table" style="background:linear-gradient(135deg,#4b5256,#9aa39f 60%,#6f7a76)"></div><div class="badge"><svg width="40" height="40" viewBox="0 0 40 40"><circle cx="20" cy="20" r="12" fill="var(--teal)" stroke="var(--teal)" stroke-width="8" stroke-dasharray="4 3"/></svg></div><div class="cap">Certifications</div></div>
  <div class="abs tile" style="left:360px"><div class="ph" role="img" aria-label="Portrait of a consultant in a suit" style="background:linear-gradient(160deg,#d9d9d7,#8b8f92 70%,#5d6266)"></div><div class="badge"><svg width="34" height="38" viewBox="0 0 34 38"><circle cx="17" cy="10" r="9" fill="var(--teal)"/><path d="M1 38c0-12 7-18 16-18s16 6 16 18z" fill="var(--teal)"/></svg></div><div class="cap">Northwind Certified<br>Trainer</div></div>
  <div class="abs tile" style="left:608px"><div class="ph" role="img" aria-label="Colleagues in a bright open office" style="background:linear-gradient(150deg,#e6e8ea,#9aa4ab 60%,#5e676d)"></div><div class="badge"><svg width="38" height="38" viewBox="0 0 38 38"><rect x="2" y="16" width="8" height="20" fill="var(--teal)"/><path d="M12 17l8-14c4 0 5 3 4 7l-1 5h10c3 0 4 3 3 5l-4 14H12z" fill="var(--teal)"/></svg></div><div class="cap">Most Valuable<br>Professional</div></div>
  <div class="abs tile" style="left:858px"><div class="ph" role="img" aria-label="Two business people shaking hands" style="background:linear-gradient(140deg,#cfd6da,#7e8b93 60%,#3d4a52)"></div><div class="badge"><svg width="46" height="36" viewBox="0 0 46 36"><circle cx="23" cy="9" r="8" fill="var(--teal)"/><circle cx="9" cy="12" r="6" fill="var(--teal)"/><circle cx="37" cy="12" r="6" fill="var(--teal)"/><path d="M10 36c0-12 6-18 13-18s13 6 13 18zM0 32c0-8 4-13 9-13 3 0 4 1 5 2-2 3-3 7-3 11zM46 32c0-8-4-13-9-13-3 0-4 1-5 2 2 3 3 7 3 11z" fill="var(--teal)"/></svg></div><div class="cap">Gold Partners</div></div>
</section>

<section class="news">
  <h2 class="abs h2" style="top:58px">NEWS</h2>
  <div class="abs news-item" style="left:110px;top:130px"><div class="ph ph-star" role="img" aria-label="Steps leading to a gold star on a dark wall"></div><div class="cap">New Gold certification obtained<br>in July 2020</div></div>
  <div class="abs news-item" style="left:612px;top:130px"><div class="ph ph-hands" role="img" aria-label="Business people shaking hands in a bright office"></div><div class="cap">Evolution of the number of certification<br>obtained by our consultants</div></div>
  <div class="abs news-item" style="left:110px;top:451px"><div class="ph ph-thumbs" role="img" aria-label="Several hands giving a thumbs up"></div><div class="cap">Arrival of a new consultant /<br>support function</div></div>
  <div class="abs news-item" style="left:612px;top:451px"><div class="ph ph-team" role="img" aria-label="Team members giving each other a high five"></div><div class="cap">Weekend / day / half–day between Brightvale.<br>Show our cooperative side, cohesive team</div></div>
</section>

<section class="testimonials">
  <h2 class="abs h2">CLIENT TESTIMONIALS</h2>
  <div class="abs client"><i></i>QUORRA</div>
  <p class="abs quote">Nemo enim ipsam voluptatem quia voluptas sit aspernatur aut odit aut fugit, sed quia cseqiu untur magni dolores eos qui ratione voluptatem sequi nesciunt. Neque porro quisquam est, qui dolorem ipsum quia dolor sit amet, consectetur, adipisci velit, sed quia non num &nbsp;eimodi tempora incidunt ut labore et dolore magnam aliquam..</p>
  <div class="abs divider"></div>
  <div class="abs avatar" role="img" aria-label="Portrait of the client spokesperson"></div>
  <div class="abs who">Jean Morel<br>CEO</div>
  <p class="abs q2">"Nam libero tempore, cum soluta nobis est eligendi opticum que nihil impedit quo minus id quod maxime placeat facere possimus, omnis voluptas assumenda est, omnis dolor rep ellendu autem quibusdam et aut ."</p>
  <div class="abs arrows">
    <i><svg width="10" height="12" viewBox="0 0 10 12"><path d="M8 1 2 6l6 5" fill="none" stroke="var(--teal)" stroke-width="2.5"/></svg></i>
    <i><svg width="10" height="12" viewBox="0 0 10 12"><path d="M2 1l6 5-6 5" fill="none" stroke="var(--teal)" stroke-width="2.5"/></svg></i>
  </div>
</section>

<footer class="site-footer">
  <div class="abs" style="left:110px;top:160px"><div class="logo">BRIGHTVALE.COOP <span class="sq"></span></div></div>
  <div class="abs fcol" style="left:470px"><h4>Information</h4><ul><li>About us</li><li>Team</li><li>Jobs</li><li>Hurry</li><li>Freelancing news</li><li>Data protection</li><li>Help</li><li>Sitemap</li></ul></div>
  <div class="abs fcol" style="left:675px"><h4>Quick Links</h4><ul><li>Offers and prices</li><li>Company</li><li>Open Brightvale coop</li><li>Insights</li><li>Create my Profile</li></ul></div>
  <div class="abs fcol" style="left:882px"><h4>Find Us</h4>
    <div class="contact"><svg width="12" height="16" viewBox="0 0 14 20"><path d="M7 0a7 7 0 0 0-7 7c0 5 7 13 7 13s7-8 7-13a7 7 0 0 0-7-7z" fill="var(--teal)"/><circle cx="7" cy="7" r="2.6" fill="#fff"/></svg><span>24 Rue des Lilas<br>75011 Paris</span></div>
    <div class="contact" style="margin-top:26px"><svg width="14" height="14" viewBox="0 0 20 20"><path d="M4 1l4 4-2 3c1 3 3 5 6 6l3-2 4 4-3 3C8 19 1 12 1 4z" fill="var(--teal)"/></svg><span>01 84 20 55 13</span></div>
    <div class="contact" style="margin-top:26px"><svg width="16" height="12" viewBox="0 0 20 14"><rect width="20" height="14" fill="var(--teal)"/><path d="M0 0l10 8 10-8" fill="none" stroke="#fff" stroke-width="1.6"/></svg><span>contact@brightvale.coop</span></div>
  </div>
  <div class="abs rule"></div>
  <p class="abs copy">© 2020, Brightvale.coop.</p>
  <div class="abs social"><i></i><i></i><i></i></div>
</footer>

</body>
</html>
```